VTMB site redesign

Please redesign a home page with content provided. PSD only - no coding
Can use any images from Snapwelder.com

Please create a site design that more clearly illustrates the client's services and expertise. We are looking for a high-end design.

Any images used must be generic or of Dallas TX.

Fonts: Any
Colors: Match to logo
Look: Modern - Professional

Target Market(s)

medium-large business owners

Number of Pages Required

1 page

Font styles to use
Serif
Sans Serif

Requirements
Must have
• cohesive professional design
• high end look
• Match to logo

```html
<!DOCTYPE html>
<html lang="en">
<head>
<meta charset="utf-8">
<title>VTMB — Veltmore Commercial Realty Group</title>
<link href="https://fonts.googleapis.com/css2?family=Oswald:wght@400;500;600&family=Poppins:wght@300;400;500;600&family=Playfair+Display:wght@600&display=swap" rel="stylesheet">
<style>
:root{
  --red:#c8232c;
  --red-dark:#a51b22;
  --ink:#222;
  --text:#555;
  --muted:#888;
  --line:#e3e3e3;
  --dark:#111;
  --footer:#0c0c0c;
  --white:#fff;
}
*{box-sizing:border-box;margin:0;padding:0}
html,body{width:1200px;height:4839px;overflow:hidden}
body{position:relative;background:var(--white);font-family:'Poppins',sans-serif;color:var(--text)}
section,header,footer{position:absolute;left:0;width:1200px}
.btn{display:inline-block;background:var(--red);color:var(--white);font:500 15px 'Poppins',sans-serif;letter-spacing:1px;text-transform:uppercase;padding:11px 26px;border-radius:2px}
.btn-outline{background:transparent;border:2px solid var(--white);padding:9px 22px}
.rule{width:60px;height:3px;background:var(--red);margin:18px auto 0}
.section-title{text-align:center;font:500 34px 'Poppins',sans-serif;color:var(--ink);letter-spacing:1px;text-transform:uppercase}

/* header */
.site-header{top:0;height:120px}
.topbar{position:absolute;left:420px;top:0;width:680px;height:32px;background:var(--red);clip-path:polygon(3% 0,97% 0,100% 100%,0 100%);color:var(--white);font:500 14px 'Poppins',sans-serif;display:flex;align-items:center;justify-content:center;gap:18px}
.topbar .dots{display:flex;gap:12px}
.topbar .dots i{width:10px;height:10px;border-radius:50%;background:var(--white);display:block}
.brand{position:absolute;left:130px;top:40px;display:flex;align-items:center;gap:12px}
.brand .square{width:30px;height:30px;background:var(--red);display:block}
.brand .name{font:600 30px 'Poppins',sans-serif;color:var(--ink);letter-spacing:2px;line-height:1}
.main-nav{position:absolute;left:455px;top:64px;display:flex;gap:28px;font:500 15px 'Poppins',sans-serif;color:var(--ink);text-transform:uppercase}

/* hero */
.hero{top:120px;height:550px}
.hero-photo{position:absolute;inset:0 0 20px 0;background:linear-gradient(180deg,#c9ccd0 0%,#9aa0a7 45%,#5c6067 100%)}
.hero-curve{position:absolute;left:0;bottom:0;width:1200px;height:80px}
.hero-card{position:absolute;left:388px;top:95px;width:426px;background:var(--white);border:8px solid rgba(255,255,255,.55);background-clip:padding-box;text-align:center;padding:30px 24px 32px}
.hero-card h1{font:600 31px/1.15 'Oswald',sans-serif;color:var(--red);text-transform:uppercase;white-space:nowrap}
.hero-card h1 span{color:var(--ink)}
.hero-card p{font:500 14px/1.55 'Poppins',sans-serif;color:var(--ink);margin:14px 10px 18px}
.arrow{position:absolute;top:270px;width:18px;height:36px}

/* why */
.why{top:670px;height:500px}
.why .section-title{margin-top:10px}
.features{position:absolute;top:160px;left:110px;width:980px;display:flex;justify-content:space-between}
.feature{width:250px;text-align:center;padding:30px 18px}
.feature.is-active{box-shadow:0 4px 18px rgba(0,0,0,.18);background:var(--white)}
.feature svg{width:70px;height:70px}
.feature h3{font:400 18px 'Poppins',sans-serif;color:var(--ink);margin:18px 0 10px}
.feature p{font:300 12px/1.7 'Poppins',sans-serif;color:var(--text)}

/* banners */
.band{height:510px}
.band-photo{position:absolute;inset:0}
.band-box{position:absolute;left:242px;width:720px;text-align:center;padding:44px 30px;border:2px solid rgba(255,255,255,.75);outline:10px solid rgba(255,255,255,.25)}
.band-box h2{font:400 23px/1.45 'Oswald',sans-serif;text-transform:uppercase;margin-bottom:24px}
.warehouse{top:1258px}
.warehouse .band-photo{background:linear-gradient(180deg,#7a2a2f 0%,#8b8d90 35%,#6e6f71 70%,#4e4f51 100%)}
.warehouse .band-box{top:150px;background:rgba(200,35,44,.88);color:var(--white)}
.lounge{top:3007px}
.lounge .band-photo{background:linear-gradient(135deg,#5a3a1c 0%,#b77a2a 40%,#d9a24a 60%,#6b4a25 100%)}
.lounge .band-box{top:158px;background:rgba(255,255,255,.9);color:var(--ink);border-color:var(--white)}

/* team */
.team{top:1840px;height:660px}
.team .section-title{margin-top:12px}
.team-intro{position:absolute;top:108px;left:150px;width:900px;text-align:center;font:300 12px/1.9 'Poppins',sans-serif;color:var(--text)}
.members{position:absolute;top:240px;left:160px;width:880px;display:flex;justify-content:space-between}
.member{width:306px;text-align:center;padding:30px 16px;height:356px}
.member.is-active{box-shadow:0 4px 18px rgba(0,0,0,.18)}
.portrait{width:172px;height:172px;border-radius:50%;margin:0 auto;border:6px solid #ececec;background:radial-gradient(circle at 50% 40%,#9b9b9b,#3a3a3a)}
.member h4{font:400 16px/1.55 'Poppins',sans-serif;color:var(--ink);margin-top:30px}
.member .social{display:flex;gap:4px;justify-content:center;margin-top:6px}
.member .social i{width:14px;height:14px;background:#2a4b8d;display:block;border-radius:2px}

/* testimonials */
.testimonials{top:2565px;height:442px;background:linear-gradient(180deg,#1b1b1b,#0a0a0a);color:var(--white);text-align:center}
.testimonials h2{font:500 32px 'Poppins',sans-serif;letter-spacing:1px;margin-top:60px;text-transform:uppercase}
.quote-mark{font:600 80px/1 'Playfair Display',serif;margin-top:14px;height:60px}
.testimonials blockquote{width:930px;margin:18px auto 0;font:300 12.5px/2 'Poppins',sans-serif;font-style:italic}
.testimonials cite{display:block;font:300 13px 'Poppins',sans-serif;font-style:italic;margin-top:16px}
.corner{position:absolute;width:60px;height:60px;border-color:var(--white);border-style:solid}
.corner.tl{left:130px;top:165px;border-width:2px 0 0 2px}
.corner.br{right:130px;top:272px;border-width:0 2px 2px 0}
.carousel-dots{display:flex;gap:8px;justify-content:center;margin-top:22px}
.carousel-dots i{width:22px;height:3px;background:#777;display:block}
.carousel-dots i.on{background:var(--white)}

/* articles */
.articles{top:3530px;height:640px}
.articles h2{text-align:center;font:300 36px 'Poppins',sans-serif;color:var(--ink);margin-top:75px;text-transform:uppercase;letter-spacing:1px}
.articles h2 b{font-weight:600}
.article-list{position:absolute;top:180px;left:129px;width:936px;display:flex;justify-content:space-between}
.article{width:298px;height:420px;border:1px solid var(--line);box-shadow:0 2px 10px rgba(0,0,0,.08)}
.article .thumb{height:180px}
.article .body{padding:18px 22px}
.article h3{font:400 14px/1.55 'Poppins',sans-serif;color:var(--ink)}
.article time{display:flex;align-items:center;gap:8px;font:400 12px 'Poppins',sans-serif;color:var(--red);margin:12px 0 10px}
.article p{font:300 11.5px/1.7 'Poppins',sans-serif;color:var(--text)}
.article .more{display:inline-block;margin-top:12px;border:1px solid var(--ink);font:500 11px 'Poppins',sans-serif;padding:4px 10px;color:var(--ink);text-transform:uppercase}

/* footer */
.site-footer{top:4170px;height:669px}
.footer-curve{position:absolute;top:0;left:0;width:1200px;height:140px}
.footer-body{position:absolute;top:120px;left:0;width:1200px;height:549px;background:var(--footer);color:var(--white)}
.footer-col{position:absolute;top:48px}
.footer-col h5{font:600 22px 'Poppins',sans-serif;margin-bottom:18px}
.footer-col h5 span{color:var(--red)}
.links li{list-style:none;font:300 13px 'Poppins',sans-serif;line-height:27px}
.links li:before{content:"›";margin-right:10px;color:#bbb}
.contact p{display:flex;gap:12px;font:300 13px/1.6 'Poppins',sans-serif;margin-bottom:12px}
.contact svg{flex:none;margin-top:3px}
.ring{display:flex;gap:6px;margin-top:4px}
.ring i{width:20px;height:20px;border:1px solid var(--white);border-radius:50%;display:block}
.quote-form p{font:300 12px/1.6 'Poppins',sans-serif;width:420px;margin-bottom:18px}
.fields{display:grid;grid-template-columns:205px 205px;gap:10px}
.fields span{display:block;height:36px;border:1px solid #666;font:300 11px/34px 'Poppins',sans-serif;padding-left:10px;color:#ccc}
.fields .submit{background:var(--red);border-color:var(--red);color:var(--white);text-align:center;font:600 14px/34px 'Poppins',sans-serif;padding:0;text-transform:uppercase}
.legal{position:absolute;top:412px;width:1200px;text-align:center;font:300 12px/2.4 'Poppins',sans-serif}
.legal a{color:var(--white);text-decoration:underline;display:block}
.legal .copy{text-decoration:none;margin-top:8px}
</style>
</head>
<body>

<header class="site-header">
  <div class="topbar">
    <span>&#9742; Call Today: 555-014-2873</span>
    <span class="dots"><i></i><i></i><i></i><i></i></span>
  </div>
  <div class="brand">
    <span class="square"></span>
    <span class="name">VTMB</span>
  </div>
  <nav class="main-nav">
    <span>Home</span><span>Services</span><span>About VTMB</span><span>Contact Us</span><span>Blog</span><span>Market News</span>
  </nav>
</header>

<section class="hero">
  <div class="hero-photo" role="img" aria-label="Bright modern office interior with desks and a city skyline view"></div>
  <svg class="arrow" style="left:110px" viewBox="0 0 18 36"><path d="M16 2 2 18l14 16" fill="none" stroke="#fff" stroke-width="2"/></svg>
  <svg class="arrow" style="right:110px" viewBox="0 0 18 36"><path d="M2 2l14 16L2 34" fill="none" stroke="#fff" stroke-width="2"/></svg>
  <svg class="hero-curve" viewBox="0 0 1200 80" preserveAspectRatio="none">
    <path d="M0 40 Q600 -10 1200 40 V80 H0Z" fill="#fff"/>
    <path d="M0 40 Q600 -10 1200 40" fill="none" stroke="#c8232c" stroke-width="4"/>
  </svg>
  <div class="hero-card">
    <h1>Professional Office<br><span>and Warehouse Leasing</span></h1>
    <p>Fast-track your search with tenant reps that only serve you, and specialize in the DFW area.</p>
    <span class="btn">Get in Touch</span>
  </div>
</section>

<section class="why">
  <h2 class="section-title">Why Tenant Representation?</h2>
  <div class="rule"></div>
  <div class="features">
    <div class="feature">
      <svg viewBox="0 0 70 70" fill="none" stroke="#c8232c" stroke-width="3"><circle cx="35" cy="14" r="8"/><circle cx="13" cy="52" r="8"/><circle cx="57" cy="52" r="8"/><path d="M35 22v14M35 36 18 46M35 36l17 10"/></svg>
      <h3>Relationships</h3>
      <p>Save time by trusting our team year after year to find the right location for you. Once we've worked together, we know what suits you.</p>
    </div>
    <div class="feature is-active">
      <svg viewBox="0 0 70 70" fill="none" stroke="#c8232c" stroke-width="3"><rect x="14" y="10" width="40" height="52" rx="3"/><rect x="26" y="5" width="16" height="9" fill="#fff"/><path d="M22 26h24M22 34h24M22 42h12"/><circle cx="50" cy="52" r="10" fill="#c8232c"/><path d="M45 52l4 4 6-7" stroke="#fff"/></svg>
      <h3>Access to More</h3>
      <p>We have no agreements or personal incentives for specific properties, so we can always show you the offices.</p>
    </div>
    <div class="feature">
      <svg viewBox="0 0 70 70" fill="none" stroke="#c8232c" stroke-width="3"><circle cx="24" cy="30" r="16"/><path d="M24 22v16M19 26h8M19 34h8"/><rect x="42" y="26" width="20" height="32" rx="10"/><path d="M52 26v10"/></svg>
      <h3>Free To You</h3>
      <p>You pay us nothing. We get our commission from the property being leased.</p>
    </div>
    <div class="feature">
      <svg viewBox="0 0 70 70" fill="none" stroke="#c8232c" stroke-width="3"><rect x="12" y="12" width="46" height="46" rx="6"/><path d="M22 36l9 9 17-19"/></svg>
      <h3>Customized Service</h3>
      <p>Aside from saving you the time of repeating what your needs are to each new location, we also provide a report of the places.</p>
    </div>
  </div>
</section>

<section class="band warehouse">
  <div class="band-photo" role="img" aria-label="Wide empty warehouse interior with red steel roof trusses"></div>
  <div class="band-box">
    <h2>If you need to find office or warehouse space in the Dallas Fort Worth area, the team at VTMB has the experience you need.</h2>
    <span class="btn btn-outline">Space Calculator</span>
  </div>
</section>

<section class="team">
  <h2 class="section-title">Meet the Team</h2>
  <div class="rule"></div>
  <p class="team-intro">At VTMB we believe that you deserve the best professional advice and personal service with your commercial real estate negotiations. By choosing VTMB as your tenant reps in the Dallas/Fort Worth area, you will receive the assistance of accomplished and experienced commercial real estate brokers and salespeople who are licensed by the State Realty Licensing Board to practice in Texas since 1983.</p>
  <div class="members">
    <div class="member">
      <div class="portrait" role="img" aria-label="Portrait photo of the founder and president"></div>
      <h4>Owen R. Veltmore<br>Founder and President</h4>
      <div class="social"><i></i><i></i><i></i></div>
    </div>
    <div class="member is-active">
      <div class="portrait" role="img" aria-label="Portrait photo of the senior director"></div>
      <h4>Daniel Ashford-Reyes,<br>Senior Director,<br>Commercial Property Specialist</h4>
      <div class="social"><i></i><i></i><i></i></div>
    </div>
    <div class="member">
      <div class="portrait" role="img" aria-label="Portrait photo of the associate tenant rep specialist"></div>
      <h4>Lucas Everett Crane,<br>Jr., Associate,<br>Tenant Rep Specialist</h4>
      <div class="social"><i></i><i></i><i></i></div>
    </div>
  </div>
</section>

<section class="testimonials">
  <h2>Client Testimonials</h2>
  <div class="quote-mark">&rdquo;</div>
  <span class="corner tl"></span><span class="corner br"></span>
  <blockquote>The real estate team at VTMB has decades of experience in Commercial. One advantage of VTMB is they know all the properties that are about to become available, BEFORE they are available. They have the inside track on properties and they watch your back at the negotiating table. Very impressive with a polished approach. Let the team run with your next project and you won't be disappointed!</blockquote>
  <cite>~Nathan Elliot Brooks</cite>
  <div class="carousel-dots"><i class="on"></i><i></i><i></i></div>
</section>

<section class="band lounge">
  <div class="band-photo" role="img" aria-label="Warm office lounge with orange armchairs and glass walls"></div>
  <div class="band-box">
    <h2>Whether your lease is expiring soon, or you're just starting your search, VTMB can help you find the perfect space.</h2>
    <span class="btn">Make an Appointment</span>
  </div>
</section>

<section class="articles">
  <h2>Recent <b>Articles</b></h2>
  <div class="article-list">
    <article class="article">
      <div class="thumb" role="img" aria-label="Warehouse aisle with tall stocked shelving" style="background:linear-gradient(180deg,#b8a48a,#6d5b45)"></div>
      <div class="body">
        <h3>Quis autem vel eum iure reprehen derit qui in ea voluptate</h3>
        <time><svg width="12" height="12" viewBox="0 0 12 12"><rect x="1" y="2" width="10" height="9" fill="none" stroke="#c8232c"/><path d="M1 5h10" stroke="#c8232c"/></svg>October 17, 2018</time>
        <p>Sed ut perspiciatis unde omnis iste natus error sit voluptatem accusantium doloremque laudan, totam rem aperiam.</p>
        <span class="more">Read More</span>
      </div>
    </article>
    <article class="article">
      <div class="thumb" role="img" aria-label="Business team standing together in an office" style="background:linear-gradient(180deg,#c4c9cf,#5f656d)"></div>
      <div class="body">
        <h3>Quis autem vel eum iure reprehen derit qui in ea voluptate</h3>
        <time><svg width="12" height="12" viewBox="0 0 12 12"><rect x="1" y="2" width="10" height="9" fill="none" stroke="#c8232c"/><path d="M1 5h10" stroke="#c8232c"/></svg>October 17, 2018</time>
        <p>Sed ut perspiciatis unde omnis iste natus error sit voluptatem accusantium doloremque laudan, totam rem aperiam.</p>
        <span class="more">Read More</span>
      </div>
    </article>
    <article class="article">
      <div class="thumb" role="img" aria-label="Open plan office with rows of desks" style="background:linear-gradient(180deg,#e3e6e8,#8d959c)"></div>
      <div class="body">
        <h3>Quis autem vel eum iure reprehen derit qui in ea voluptate</h3>
        <time><svg width="12" height="12" viewBox="0 0 12 12"><rect x="1" y="2" width="10" height="9" fill="none" stroke="#c8232c"/><path d="M1 5h10" stroke="#c8232c"/></svg>October 17, 2018</time>
        <p>Sed ut perspiciatis unde omnis iste natus error sit voluptatem accusantium doloremque laudan, totam rem aperiam.</p>
        <span class="more">Read More</span>
      </div>
    </article>
  </div>
</section>

<footer class="site-footer">
  <svg class="footer-curve" viewBox="0 0 1200 140" preserveAspectRatio="none">
    <path d="M0 40 Q600 150 1200 40 V140 H0Z" fill="#0c0c0c"/>
    <path d="M0 40 Q600 150 1200 40" fill="none" stroke="#c8232c" stroke-width="5"/>
  </svg>
  <div class="footer-body">
    <div class="footer-col" style="left:130px">
      <h5>Quick <span>Links</span></h5>
      <ul class="links"><li>Home</li><li>Services</li><li>About VTMB</li><li>Contact Us</li><li>Blog</li><li>Market News</li></ul>
    </div>
    <div class="footer-col contact" style="left:340px;width:260px">
      <h5>Contact <span>Us</span></h5>
      <p><svg width="12" height="16" viewBox="0 0 12 16"><path d="M6 15S1 9 1 6a5 5 0 0 1 10 0c0 3-5 9-5 9z" fill="#fff"/><circle cx="6" cy="6" r="2" fill="#0c0c0c"/></svg><span>VTMB<br>412 Harwell Avenue, Suite 300,<br>Dallas, TX 75201</span></p>
      <p><svg width="12" height="14" viewBox="0 0 12 14"><path d="M2 1h3l1 3-2 1.5a7 7 0 0 0 3.5 3.5L9 7l3 1v3c0 1-1 2-2 2A10 10 0 0 1 1 3c0-1 .5-2 1-2z" fill="#fff"/></svg><span>Phone 555-014-2873<br>Fax 555-014-2874</span></p>
      <p><svg width="13" height="10" viewBox="0 0 13 10"><rect x=".5" y=".5" width="12" height="9" fill="none" stroke="#fff"/><path d="M.5.5l6 5 6-5" fill="none" stroke="#fff"/></svg><span>Email: info@vtmb-realty.com</span></p>
      <div class="ring"><i></i><i></i><i></i><i></i></div>
    </div>
    <div class="footer-col quote-form" style="left:632px">
      <h5>Get a <span>Quote</span></h5>
      <p>Lorem ipsum dolor sit amet, consectetur adipiscing elit, sed do eiusmod tempor incididunt ut labore et dolore magna aliqua.</p>
      <div class="fields"><span>Name</span><span>E-Mail</span><span>Phone No</span><span class="submit">Submit</span></div>
    </div>
    <div class="legal">
      <a>State Realty Licensing Board Information About Brokerage Services</a>
      <a>State Realty Licensing Board Consumer Protection Notice</a>
      <a class="copy">© 2018 Veltmore Commercial Realty Group. All Rights Reserved.</a>
    </div>
  </div>
</footer>

</body>
</html>
```